Laser Tattoo Removal Business Cards

We are looking for a professional business card design for a laser tattoo removal business. Ideally looking for a black business card design. The name of the business is Brightline Tattoo Removal. We place our cards at local tattoo shops so we ideally are looking for something trendy/edgy to draw both male and female clientele in.

Target Market(s)

Male/Female ages 18-60

Contact Information for Business Card

black background ideally.. hoping to stay within greys, whites and black

Font styles to use
Serif
Sans Serif

Colors
121212
a9a9a9
5c5c5c
f5f5f5
ffffff
7f7f7f
606060
848484
9d9d9d

Requirements
Must have
• Employee Info:
• Melissa Thornbury
• Chief Executive Offer
• m: 919.537.2846
• w: 919.362.4178
• f: 919.685.3907
• mthornbury@brightlinetattooremoval.example
• Address:
• 4615 Oakmere Pkwy, Suite 210
• Raleigh, NC 27654
• Website:
• www.brightlinetattooremoval.example
Nice to have
• Myabe business name on back or logo on back and employee info on the front

```html
<!DOCTYPE html>
<html lang="en">
<head>
<meta charset="utf-8">
<title>Brightline Tattoo Removal – Business Cards</title>
<link href="https://fonts.googleapis.com/css2?family=Josefin+Sans:wght@400&family=Roboto:wght@400;700&display=swap" rel="stylesheet">
<style>
  :root {
    --ink: #121212;
    --paper: #f5f5f5;
    --white: #ffffff;
    --grey-light: #a9a9a9;
    --grey-mid: #7f7f7f;
    --grey-dark: #5c5c5c;
    --stage: #3a3431;
  }
  * { margin: 0; padding: 0; box-sizing: border-box; }
  html, body { width: 1200px; height: 769px; overflow: hidden; }
  body {
    background: var(--stage);
    position: relative;
    font-family: "Roboto", Arial, sans-serif;
  }
  .card {
    position: absolute;
    top: 230px;
    width: 540px;
    height: 309px;
    border-radius: 3px;
    overflow: hidden;
  }
  .card--front { left: 40px; background: var(--paper); }
  .card--back { left: 620px; background: var(--ink); }

  .brand {
    position: absolute;
    display: flex;
    flex-direction: column;
    align-items: center;
    font-family: "Josefin Sans", Arial, sans-serif;
    font-weight: 400;
  }
  .brand__name {
    font-size: 38px;
    letter-spacing: 4px;
    line-height: 1;
  }
  .brand__mark {
    width: 12px; height: 12px;
    border: 1px solid currentColor;
    margin: 12px 0 10px;
  }
  .brand__tagline {
    display: flex;
    align-items: center;
    gap: 8px;
  }
  .brand__sub {
    font-size: 15px;
    letter-spacing: 3px;
    line-height: 1;
  }
  .brand__rule { width: 16px; height: 1px; background: currentColor; }

  .card--front .brand { left: 0; width: 292px; top: 100px; color: var(--ink); }
  .card--front .brand__mark,
  .card--front .brand__rule { color: var(--grey-dark); }

  .card--back .brand { left: 0; right: 0; top: 88px; color: var(--grey-light); }

  .website {
    position: absolute;
    left: 0; right: 0;
    bottom: 70px;
    text-align: center;
    color: var(--white);
    font-size: 12px;
    letter-spacing: 2px;
  }

  .contact-panel {
    position: absolute;
    right: 0;
    top: 28px;
    bottom: 28px;
    width: 248px;
    background: var(--ink);
    color: var(--white);
    padding: 20px 14px 0 18px;
  }
  .contact-panel__name {
    font-weight: 700;
    font-size: 16px;
    letter-spacing: 0.3px;
  }
  .contact-panel__title { font-size: 12px; margin-bottom: 8px; color: var(--paper); }
  .contact-panel__address { font-size: 12px; line-height: 1.3; margin-bottom: 8px; }
  .contact-list { list-style: none; }
  .contact-list li {
    display: flex;
    align-items: center;
    gap: 7px;
    font-size: 12px;
    line-height: 17px;
    white-space: nowrap;
  }
  .contact-list li.small { font-size: 10.2px; }
  .contact-list svg { width: 11px; height: 11px; flex: none; fill: var(--white); }
</style>
</head>
<body>

  <section class="card card--front">
    <div class="brand">
      <div class="brand__name">BRIGHTLINE</div>
      <div class="brand__mark"></div>
      <div class="brand__tagline">
        <span class="brand__rule"></span>
        <span class="brand__sub">TATTOO REMOVAL</span>
        <span class="brand__rule"></span>
      </div>
    </div>

    <div class="contact-panel">
      <div class="contact-panel__name">MELISSA THORNBURY</div>
      <div class="contact-panel__title">Chief Executive Offer</div>
      <div class="contact-panel__address">4615 Oakmere Pkwy, Suite 210<br>Raleigh, NC 27654</div>
      <ul class="contact-list">
        <li><svg viewBox="0 0 24 24" aria-hidden="true"><path d="M6.6 10.8a15 15 0 0 0 6.6 6.6l2.2-2.2c.3-.3.7-.4 1-.2 1.1.4 2.3.6 3.6.6.6 0 1 .4 1 1V20c0 .6-.4 1-1 1A17 17 0 0 1 3 4c0-.6.4-1 1-1h3.5c.6 0 1 .4 1 1 0 1.3.2 2.5.6 3.6.1.3 0 .7-.2 1z"/></svg>919.362.4178</li>
        <li><svg viewBox="0 0 24 24" aria-hidden="true"><path d="M7 1h10a2 2 0 0 1 2 2v18a2 2 0 0 1-2 2H7a2 2 0 0 1-2-2V3a2 2 0 0 1 2-2zm0 3v14h10V4zm5 15.5a1.2 1.2 0 1 0 0 2.4 1.2 1.2 0 0 0 0-2.4z"/></svg>919.537.2846</li>
        <li><svg viewBox="0 0 24 24" aria-hidden="true"><path d="M6 2h10v6H6zM3 9h18a1 1 0 0 1 1 1v9a1 1 0 0 1-1 1H3a1 1 0 0 1-1-1v-9a1 1 0 0 1 1-1zm4 5v4h10v-4z"/></svg>919.685.3907</li>
        <li class="small"><svg viewBox="0 0 24 24" aria-hidden="true"><path d="M2 5h20v14H2zm2 2v.5l8 5 8-5V7zm0 2.8V17h16V9.8l-8 5z"/></svg>mthornbury@brightlinetattooremoval.example</li>
        <li class="small"><svg viewBox="0 0 24 24" aria-hidden="true"><path d="M12 2a10 10 0 1 0 0 20 10 10 0 0 0 0-20zm0 2c1 0 2.3 2 2.8 5H9.2C9.7 6 11 4 12 4zM4.3 11h4.7c0 .7 0 1.4.1 2H4.3a8 8 0 0 1 0-2zm5 4h5.4c-.5 3-1.7 5-2.7 5s-2.2-2-2.7-5zm6.6-2c.1-.6.1-1.3.1-2h3.7a8 8 0 0 1 0 2z"/></svg>www.brightlinetattooremoval.example</li>
      </ul>
    </div>
  </section>

  <section class="card card--back">
    <div class="brand">
      <div class="brand__name">BRIGHTLINE</div>
      <div class="brand__mark"></div>
      <div class="brand__tagline">
        <span class="brand__rule"></span>
        <span class="brand__sub">TATTOO REMOVAL</span>
        <span class="brand__rule"></span>
      </div>
    </div>
    <div class="website">www.brightlinetattooremoval.example</div>
  </section>

</body>
</html>
```